Building Design company needing a letterhead

We need a letter head for our Building Design company to send letters etc. to our clients, consultants, councils etc. We would like to see our logo used and company colours. I have attached our style guide and an example of our current letterheads. Top left we would like our logo, top right we would like the company details and at the footer we would like some sort of image/design etc. that suits our brand. I like the Tarrow Design letterhead attached.

Target Market(s)

Professionals, Councils, Consultants, Mums & Dads

Industry/Entity Type

Architecture

Other font styles liked:
• refer the design style guide

Colors
f37122
000000
1b1b1b

Requirements
Must have
• Must have the minimum of a logo, company details and footer
Nice to have
• An image/design made for the footer that would suite our brand and website at www.corvanplans.com.au. Also it would be nice to include the KMEOT logo somewhere perhaps included in the footer.
Should not have
• Large images in the header. I just want the logo and company details.

```html
<!DOCTYPE html>
<html lang="en">
<head>
<meta charset="utf-8">
<title>Marrick Design – Letterhead</title>
<link href="https://fonts.googleapis.com/css2?family=Titillium+Web:wght@400;600&family=Questrial&display=swap" rel="stylesheet">
<style>
  :root {
    --backdrop: #878787;
    --paper: #ffffff;
    --orange-deep: #e4592a;
    --orange-soft: #ee8049;
    --ink: #1b1b1b;
    --on-orange: #ffffff;
    --ghost: #f2f2f2;
  }
  * { box-sizing: border-box; margin: 0; padding: 0; }
  html, body { width: 847px; height: 1200px; overflow: hidden; }
  body { background: var(--backdrop); position: relative; font-family: "Questrial", sans-serif; }

  .letterhead {
    position: absolute; left: 70px; top: 70px;
    width: 708px; height: 1059px;
    background: var(--paper);
    overflow: hidden;
  }

  .watermark {
    position: absolute; left: 26px; top: 615px; z-index: 0;
    transform: rotate(-31deg); transform-origin: left top;
    font-family: "Titillium Web", sans-serif; font-weight: 600;
    color: var(--ghost); text-transform: uppercase;
    font-size: 128px; line-height: 112px; letter-spacing: 10px;
    white-space: nowrap;
  }
  .watermark span { display: block; }
  .watermark span + span { padding-left: 90px; }

  .header-wave { position: absolute; left: 0; top: 0; width: 708px; height: 140px; z-index: 1; }

  .brand {
    position: absolute; left: 57px; top: 60px; z-index: 2;
    display: flex; align-items: center; gap: 14px;
  }
  .brand-square { width: 34px; height: 34px; background: var(--orange-deep); }
  .brand-name {
    font-family: "Titillium Web", sans-serif; font-weight: 600;
    font-size: 27px; line-height: 24px; letter-spacing: 1px;
    color: var(--ink); text-transform: uppercase;
  }

  .contact {
    position: absolute; right: 34px; top: 16px; z-index: 2;
    text-align: right; color: var(--on-orange);
    font-variant: small-caps; letter-spacing: 1.5px;
  }
  .contact-name { font-size: 13px; line-height: 14px; }
  .contact-role { font-size: 11px; line-height: 14px; margin-bottom: 7px; }
  .contact-name, .contact-role { margin-right: 16px; }
  .contact-line {
    display: flex; justify-content: flex-end; align-items: center; gap: 7px;
    font-size: 11px; line-height: 17px;
  }
  .contact-line svg { width: 9px; height: 9px; }

  .footer-band {
    position: absolute; left: 0; bottom: 0; width: 708px; height: 72px; z-index: 2;
    background: linear-gradient(to bottom, var(--orange-deep), var(--orange-soft));
    color: var(--on-orange); text-align: center;
    font-variant: small-caps; letter-spacing: 1.5px; font-size: 11px; line-height: 18px;
    padding-top: 20px;
  }
</style>
</head>
<body>
  <main class="letterhead">
    <div class="watermark" aria-hidden="true">
      <span>Marrick</span>
      <span>Design</span>
    </div>

    <svg class="header-wave" viewBox="0 0 708 140" aria-hidden="true">
      <defs>
        <linearGradient id="headerFill" x1="0" y1="0" x2="0" y2="1">
          <stop offset="0" stop-color="#e4592a"/>
          <stop offset="1" stop-color="#ee8049"/>
        </linearGradient>
      </defs>
      <path d="M0 0 H708 V95 C655 122 600 134 538 133 C440 131 360 80 275 42 C215 16 150 14 95 38 C55 55 25 72 0 90 Z" fill="url(#headerFill)"/>
    </svg>

    <div class="brand">
      <div class="brand-square"></div>
      <div class="brand-name">Marrick<br>Design</div>
    </div>

    <div class="contact">
      <div class="contact-name">John Smith</div>
      <div class="contact-role">Designation</div>
      <div class="contact-line">(123) 456-7890
        <svg viewBox="0 0 10 10"><path d="M2 0.5 L3.8 2.6 L2.9 3.6 C3.5 5 4.6 6.3 6.2 7 L7.2 6 L9.4 7.8 L8.2 9.5 C4.5 9 1 5.5 0.6 1.8 Z" fill="#fff"/></svg>
      </div>
      <div class="contact-line">info@companyname.com
        <svg viewBox="0 0 10 10"><rect x="0.5" y="2" width="9" height="6.5" fill="#fff"/><path d="M0.8 2.3 L5 5.6 L9.2 2.3" stroke="#e4592a" stroke-width="0.9" fill="none"/></svg>
      </div>
      <div class="contact-line">companyname.com
        <svg viewBox="0 0 10 10" fill="none" stroke="#fff" stroke-width="0.8"><circle cx="5" cy="5" r="4.3"/><ellipse cx="5" cy="5" rx="1.8" ry="4.3"/><path d="M0.7 5 H9.3 M1.5 2.7 H8.5 M1.5 7.3 H8.5"/></svg>
      </div>
    </div>

    <footer class="footer-band">
      <div>Address line1, address line2</div>
      <div>country - 123456</div>
    </footer>
  </main>
</body>
</html>
```